Advertising Portal Needs eBrochure

Hi Crowders! Our advertising portal, which focus on the new launches property, needs an online brochure to promote to potential advertisers the benefits of advertising their projects with us. These advertisers will be mainly real estate developers and agencies.

WHAT WE LOOKING FOR
We do not want over-fanciful designs that makes the content hard to read. The use of illustrations and graphics/symbols related to covered topics are encouraged. The overall design should portrait our advertising efficiency through online and social media means. Our website - www.brightkeyhomes.sg.

For draft purposes, just do up the front page, back page, and few inner pages, preferably to include one illustration chart (either on page 7/8). Size wise probably A5 portrait or landscape, for future printing into a booklet.

WORK COMPLETION AND PAYMENT
The $500 stated here is 50% of the payment. Upon getting a desired draft design, we will need you to work on the full content with slight amendments along the way. Once done, we will be paying the balance $500, and we will need the pdf file as well as the work file.

Let your design juice flow, and hope we can work with you!
Updates

Hi Crowders! Thank you for your submissions. We are closing the project as we've decided on a design. It's a pity we can only select one design, as there are a number of good works. Hope we will have a chance to work together on our upcoming projects. Cheers =)

Target Market(s)

Real estate developers, real estate agencies, and perhaps to an extent, individual property sales agent.

Industry/Entity Type

Advertising

Requirements
Should not have
• We prefer not to have much real people kind of stock images. Try not to use images from our portal as we do not have the ownerships. Instead, you can use stock images of property developments artist impression that gives a similar feel.

```html
<!DOCTYPE html>
<html lang="en">
<head>
<meta charset="utf-8">
<title>BrightKeyHomes.sg – Step 3</title>
<link href="https://fonts.googleapis.com/css2?family=Josefin+Sans:ital,wght@0,300;0,400;0,600;0,700;1,400;1,700&display=swap" rel="stylesheet">
<style>
  :root{
    --bg:#9a9a9a;
    --paper:#fbfbfa;
    --green:#5aab3f;
    --green-light:#8cc63f;
    --ink:#3a3a3a;
    --muted:#777;
    --line:#555;
  }
  *{margin:0;padding:0;box-sizing:border-box}
  html,body{width:1200px;height:800px;overflow:hidden}
  body{background:var(--bg);font-family:"Josefin Sans",sans-serif;color:var(--ink);position:relative}
  .page{position:absolute;top:30px;width:560px;height:740px;background:var(--paper);overflow:hidden}
  .page--left{left:40px;box-shadow:inset -18px 0 24px -18px rgba(0,0,0,.18)}
  .page--right{left:600px;box-shadow:inset 18px 0 24px -18px rgba(0,0,0,.18)}
  .step-tag{position:absolute;top:78px;left:0;width:190px;height:30px;background:var(--green);color:#fff;font-weight:700;font-size:17px;line-height:32px;padding-left:52px;clip-path:polygon(0 0,100% 0,92% 50%,100% 100%,0 100%)}
  .page-title{position:absolute;top:128px;left:58px;width:460px;font-weight:300;font-size:38px;line-height:1.08;color:#444}
  .lead{position:absolute;top:262px;left:58px;width:440px;font-style:italic;font-size:12px;line-height:1.6;color:var(--muted)}
  .section-title{font-weight:700;font-size:19px;line-height:1.2;color:#222;margin-bottom:4px}
  .cross-traffic{position:absolute;top:316px;left:58px;width:450px}
  .cross-traffic p{font-style:italic;font-size:12px;line-height:1.6;color:var(--muted)}
  .skyline-art{position:absolute;top:420px;left:40px;width:480px;height:300px;border-radius:30px 30px 0 0;background:linear-gradient(180deg,#b9dc7a 0%,#7dbb45 55%,#6fb8c9 100%)}
  .diagram-title{position:absolute;top:78px;left:0;width:560px;text-align:center;font-style:italic;font-weight:700;font-size:15px;line-height:1.3;color:var(--green)}
  .diagram{position:absolute;top:120px;left:47px}
  .content{position:absolute;top:336px;left:50px;width:470px;display:flex;flex-direction:column;gap:12px}
  .copy p{font-size:11.5px;line-height:1.5;color:#555}
  .copy .note{margin-top:4px}
  .coming-soon{margin-top:6px;background:linear-gradient(90deg,#6fb33f,var(--green-light));padding:12px 22px 12px;color:#2c3a1c}
  .coming-soon h3{font-size:17px;font-weight:700;margin-bottom:6px}
  .coming-soon p{font-size:11.5px;line-height:1.5}
  .coming-soon ul{margin-top:3px;padding-left:14px;font-size:11px;line-height:1.55}
</style>
</head>
<body>
  <section class="page page--left">
    <div class="step-tag">Step 3</div>
    <h1 class="page-title">Your Project Gains<br>Huge Awareness From<br>BrightKeyHomes.sg</h1>
    <p class="lead">Even when your project isn't actively marketing, it will still receive great interest and awareness from quality consumers, and here is how.</p>
    <div class="cross-traffic">
      <h2 class="section-title">Cross traffic</h2>
      <p>The marketing campaigns on the many other projects will generates high number of visitors to our portal, and these visitors has a high chance to see your project as well.</p>
    </div>
    <div class="skyline-art" role="img" aria-label="Illustration of green skyscrapers surrounded by speech bubbles with social and messaging icons"></div>
  </section>

  <section class="page page--right">
    <h2 class="diagram-title">How Your Project Gains Constant Awareness<br>From BrightKeyHomes.sg</h2>
    <svg class="diagram" width="466" height="210" viewBox="0 0 520 235" font-family="Josefin Sans, sans-serif">
      <defs>
        <marker id="arrow" markerWidth="6" markerHeight="6" refX="5" refY="3" orient="auto">
          <path d="M0,0 L6,3 L0,6 Z" fill="#555"/>
        </marker>
      </defs>
      <rect x="100" y="2" width="280" height="40" rx="8" fill="#fff" stroke="#555" stroke-width="2"/>
      <text x="150" y="27" font-size="14" font-weight="700" fill="#444" text-anchor="middle">Friendloop</text>
      <text x="240" y="27" font-size="14" font-weight="700" fill="#444" text-anchor="middle">Searchly</text>
      <text x="328" y="27" font-size="14" font-weight="700" fill="#444" text-anchor="middle">Daily Ledger</text>
      <text x="240" y="60" font-size="10" font-weight="700" fill="#333" text-anchor="middle">Marketing activities for many other projects in BrightKeyHomes</text>
      <g stroke="#555" stroke-width="1.2" marker-end="url(#arrow)">
        <line x1="80" y1="66" x2="80" y2="86"/><line x1="140" y1="66" x2="140" y2="86"/>
        <line x1="200" y1="66" x2="200" y2="86"/><line x1="280" y1="66" x2="280" y2="86"/>
        <line x1="340" y1="66" x2="340" y2="86"/><line x1="400" y1="66" x2="400" y2="86"/>
      </g>
      <g fill="#666" stroke="#444">
        <rect x="67" y="92" width="26" height="28"/><rect x="127" y="92" width="26" height="28"/>
        <rect x="187" y="92" width="26" height="28"/><rect x="267" y="92" width="26" height="28"/>
        <rect x="327" y="92" width="26" height="28"/><rect x="387" y="92" width="26" height="28"/>
      </g>
      <g font-size="8" font-weight="700" fill="#333" text-anchor="middle">
        <text x="80" y="132">Project1</text><text x="140" y="132">Project2</text>
        <text x="200" y="132">Project3</text><text x="280" y="132">Project4</text>
        <text x="340" y="132">Project5</text><text x="400" y="132">Project6</text>
      </g>
      <g stroke="#555" stroke-width="1.2" fill="none" marker-end="url(#arrow)">
        <path d="M80,138 V150 H140 V166"/>
        <line x1="200" y1="138" x2="200" y2="166"/>
        <line x1="280" y1="138" x2="280" y2="166"/>
        <path d="M400,138 V150 H340 V166"/>
      </g>
      <text x="240" y="155" font-size="10" font-weight="700" fill="#333" text-anchor="middle">Huge Traffics Flows To</text>
      <rect x="110" y="170" width="260" height="44" rx="8" fill="#fff" stroke="#555" stroke-width="2"/>
      <circle cx="134" cy="192" r="8" fill="#5aab3f"/>
      <text x="252" y="199" font-size="20" font-weight="700" fill="#5aab3f" text-anchor="middle">brightkeyhomes.sg</text>
      <line x1="374" y1="192" x2="418" y2="192" stroke="#555" stroke-width="1.2" marker-end="url(#arrow)"/>
      <rect x="424" y="160" width="66" height="66" rx="8" fill="#eee" stroke="#555" stroke-width="1.5"/>
      <rect x="442" y="168" width="30" height="32" fill="#c0392b"/>
      <text x="457" y="216" font-size="8" font-weight="700" fill="#333" text-anchor="middle">Your Project</text>
    </svg>

    <div class="content">
      <div class="copy quality">
        <h2 class="section-title">Quality visitors</h2>
        <p>As our portal is dedicated solely on the new launches property, visitors to BrightKeyHomes.sg are probably interested in new property and a good chance they will be interested in your project. And as showed by our extremely low bounce rate, they don't simply come and go after landing on any of our page.</p>
        <p class="note">[Illustration to compare our 1% bounce rate to 10% average]</p>
      </div>
      <div class="copy growth">
        <h2 class="section-title">Fast growth in BrightKeyHomes.Sg</h2>
        <p>All these marketing campaigns also means the public will take notice of our portal very fast, and with our neat interface, user friendly features, reliable and updated content, we are absolutely certain to have an exponential growth in viewership, in order to bring to you more quality visitors on your project very soon.</p>
      </div>
      <div class="coming-soon">
        <h3>Coming soon</h3>
        <p>BrightKeyHomes.sg is continually improving. We're planning a major update to the portal soon, to make it even better with:</p>
        <ul>
          <li>Enhanced features</li>
          <li>Improved functionality</li>
          <li>An even more useful, user friendly interface</li>
          <li>More marketing packages</li>
        </ul>
      </div>
    </div>
  </section>
</body>
</html>
```